Vantiqo custom business card design

Need a authentic, innovative business card design for a new mobile app business. I am uploading a few screen images from our app for you to view. I would like app design theme to match business card design. I can also send logo images.

```html
<!DOCTYPE html>
<html lang="en">
<head>
<meta charset="UTF-8">
<title>Vantiqo Business Card</title>
<link href="https://fonts.googleapis.com/css2?family=Work+Sans:wght@400;500;700&display=swap" rel="stylesheet">
<style>
  :root {
    --page-bg: #ece8e2;
    --card-bg: #2a2725;
    --ink: #e4d8c8;
    --ink-soft: #cfc3b3;
    --brand-purple: #5b2781;
  }
  html, body {
    margin: 0;
    padding: 0;
    width: 1200px;
    height: 811px;
    overflow: hidden;
    background: var(--page-bg);
    font-family: "Work Sans", Arial, sans-serif;
  }
  .card {
    position: absolute;
    left: 100px;
    top: 135px;
    width: 1000px;
    height: 540px;
    border-radius: 22px;
    background: var(--card-bg);
    overflow: hidden;
    color: var(--ink);
  }
  .brand-mark {
    position: absolute;
    right: 110px;
    top: 57px;
    width: 440px;
    height: 440px;
    border-radius: 50%;
    background: var(--brand-purple);
  }
  .wordmark {
    position: absolute;
    left: 48px;
    top: 30px;
    margin: 0;
    font-size: 74px;
    font-weight: 700;
    letter-spacing: 0.5px;
    color: var(--ink);
  }
  .person-name {
    position: absolute;
    left: 48px;
    top: 178px;
    margin: 0;
    font-size: 36px;
    font-weight: 500;
    letter-spacing: 1px;
  }
  .person-title {
    position: absolute;
    left: 48px;
    top: 226px;
    margin: 0;
    font-size: 26px;
    color: var(--ink-soft);
  }
  .address {
    position: absolute;
    left: 48px;
    top: 268px;
    margin: 0;
    font-style: normal;
    font-size: 26px;
    line-height: 37px;
    color: var(--ink-soft);
  }
  .contact-list {
    position: absolute;
    left: 48px;
    top: 362px;
    margin: 0;
    padding: 0;
    list-style: none;
    font-size: 26px;
    line-height: 37px;
    color: var(--ink-soft);
  }
  .contact-list li {
    display: flex;
    align-items: center;
    gap: 14px;
  }
  .contact-icon {
    width: 20px;
    height: 20px;
    fill: none;
    stroke: var(--ink-soft);
    stroke-width: 2;
  }
</style>
</head>
<body>
  <div class="card">
    <div class="brand-mark"></div>
    <h1 class="wordmark">Vantiqo</h1>
    <p class="person-name">DANIEL FOSTER</p>
    <p class="person-title">Director</p>
    <address class="address">1275 Harbor Lane<br>Coral Bay, FL 32190</address>
    <ul class="contact-list">
      <li>
        <svg class="contact-icon" viewBox="0 0 20 20"><rect x="5" y="2" width="10" height="16" rx="1.5"/><line x1="9" y1="15" x2="11" y2="15"/></svg>
        (555) 410-2287
      </li>
      <li>
        <svg class="contact-icon" viewBox="0 0 20 20"><path d="M5 3 L8 3 L9 7 L7 8.5 C8 11 9 12 11.5 13 L13 11 L17 12 L17 15 C17 16 16 17 15 17 C9 17 3 11 3 5 C3 4 4 3 5 3 Z"/></svg>
        (555) 638-9021
      </li>
      <li>
        <svg class="contact-icon" viewBox="0 0 20 20"><rect x="2.5" y="5" width="15" height="10" rx="1"/><polyline points="2.5,5.5 10,11 17.5,5.5"/></svg>
        info@Vantiqo.com
      </li>
      <li>
        <svg class="contact-icon" viewBox="0 0 20 20"><circle cx="10" cy="10" r="7.5"/><ellipse cx="10" cy="10" rx="3.2" ry="7.5"/><line x1="2.5" y1="10" x2="17.5" y2="10"/></svg>
        www.Vantiqo.com
      </li>
    </ul>
  </div>
</body>
</html>
```